Web Design for a Biotech Consulting Firm

We need a web site design for a new business based in Philadelphia called Verantel Dx. This is a consulting firm that will serve medical diagnostics industry, which is part of the life science/healthcare industry focusing on developing and marketing products that help in early detection, monitoring or management of diseases. Our consulting firm will help medical diagnostic companies to overcome key challenges in designing, evaluating and marketing new products.Our company name is Verantel Dx. Verantel is Latin word for "something" Dx represents diagnostics. The idea behind the name is that we help companies to transform the original, early product ideas ("nothing") into "something"; which is a product with full clinical utility that will help to improve health and well-being.The web site should use the visual feel of the logo (attached), be modern, simple and clean looking and represent creativity, innovation, scientific thinking and progress.
Updates

Wix Design is acceptable

Industry/Entity Type

Biotechnology

Coding

Coded - Design and coding required

Number of Pages Required

1 page

Font styles to use
Sans Serif

Requirements
Must have
• simple, clean look couple of pages
Should not have
• a lot of pages

```html
<!DOCTYPE html>
<html lang="en">
<head>
<meta charset="utf-8">
<title>Verantel Dx — Medical Diagnostics Consulting</title>
<link href="https://fonts.googleapis.com/css2?family=Mulish:wght@400;500;600;700&family=Open+Sans:wght@400;600;700&display=swap" rel="stylesheet">
<style>
:root{
  --ink:#1b1f4a;
  --navy:#141a55;
  --blue:#1a5cf2;
  --blue-bright:#2f7cf6;
  --blue-deep:#0f3fe0;
  --text:#444a5c;
  --muted:#6b7080;
  --white:#ffffff;
  --footer:#121212;
}
*{box-sizing:border-box;margin:0;padding:0}
html,body{width:1200px;height:3059px;overflow:hidden}
body{position:relative;background:var(--white);font-family:"Mulish",sans-serif;color:var(--text)}
.abs{position:absolute}

/* hero */
.topbar{left:0;top:0;width:1200px;height:21px;background:#000}
.hero{left:0;top:21px;width:1200px;height:753px;
  background:radial-gradient(ellipse at 60% 35%,#3d6bff 0%,#1f3fc9 30%,#16238a 60%,#0d1250 100%);
  clip-path:polygon(0 0,1200px 0,1200px 673px,1030px 673px,930px 690px,760px 700px,700px 716px,605px 753px,520px 716px,430px 700px,320px 690px,230px 695px,130px 673px,0 673px)}
.brand{left:162px;top:66px;display:flex;align-items:center;gap:10px;color:var(--white)}
.brand-square{width:12px;height:12px;background:var(--blue-bright)}
.brand-name{font-size:28px;font-weight:500;white-space:nowrap}
.nav{top:71px;left:388px;display:flex;gap:34px;font-size:16px;color:var(--white);white-space:nowrap}
.social{top:28px;left:896px;display:flex;gap:34px}
.social span{width:20px;height:20px;border:2px solid var(--white);border-radius:50%}
.hero-title{left:152px;top:296px;font-size:51px;line-height:55px;font-weight:700;color:var(--white)}
.btn{display:flex;align-items:center;justify-content:center;color:var(--white);background:linear-gradient(90deg,var(--blue-bright),var(--blue-deep));font-weight:500;white-space:nowrap}
.hero-btn{left:158px;top:427px;width:174px;height:48px;font-size:17px}
.dots{left:531px;top:669px;display:flex;gap:6px}
.dots i{display:block;width:40px;height:2px;background:rgba(255,255,255,.4)}
.dots i:first-child{background:var(--white)}

/* what we do */
.section-title{font-size:38px;font-weight:400;color:var(--ink)}
.wwd-title{left:0;width:1200px;top:822px;text-align:center}
.wwd-lead{left:0;width:1200px;top:882px;text-align:center;font-size:18px;line-height:27px;color:var(--text)}
.service{border:2px solid var(--blue);width:266px;height:280px;background:var(--white)}
.service h3{position:absolute;left:51px;font-size:23px;line-height:22px;font-weight:700;color:var(--navy)}
.service p{position:absolute;left:51px;width:200px;font-size:13.5px;line-height:20px;color:var(--muted)}
.service .btn{position:absolute;left:51px;width:135px;height:38px;font-size:13px}
.service svg{position:absolute;left:-30px;background:var(--white)}

/* about */
.about-photo{left:0;top:1364px;width:710px;height:517px;background:linear-gradient(135deg,#eef2fb 0%,#c9d4ef 40%,#8fa3d6 70%,#dfe6f6 100%)}
.about-card{left:557px;top:1436px;width:542px;height:371px;background:linear-gradient(135deg,var(--blue-bright),var(--blue-deep));color:var(--white);padding:48px 36px 0 54px}
.about-card h2{font-size:39px;font-weight:400;margin-bottom:14px}
.about-card p{font-size:16px;line-height:23px;margin-bottom:13px}
.outline-btn{margin-top:14px;width:175px;height:48px;border:2px solid var(--white);display:flex;align-items:center;justify-content:center;font-size:17px;font-weight:500}

/* blogs */
.blog-title{left:161px;top:1940px}
.post{width:290px;height:357px;top:2017px;background:var(--white);box-shadow:0 4px 14px rgba(0,0,0,.08)}
.post-img{position:absolute;left:0;top:0;width:290px;height:169px}
.post-date{position:absolute;left:22px;top:187px;width:52px;height:45px;background:var(--blue);color:var(--white);text-align:center;line-height:17px;padding-top:5px}
.post-date b{display:block;font-size:21px;font-weight:500;line-height:21px}
.post-date span{font-size:14px}
.post h4{position:absolute;left:86px;top:186px;width:190px;font-size:18px;line-height:23px;font-weight:500;color:var(--blue)}
.post p{position:absolute;left:23px;top:256px;width:250px;font-family:"Open Sans",sans-serif;font-size:12px;line-height:19px;color:var(--muted)}
.post .more{position:absolute;left:23px;top:323px;font-family:"Open Sans",sans-serif;font-size:12.5px;font-weight:700;color:#111}

/* contact */
.contact{left:0;top:2449px;width:1200px;height:451px;background:linear-gradient(180deg,#2b2b2d,#1a1a1c)}
.contact-title{left:0;width:1212px;top:2496px;text-align:center;color:var(--white)}
.field{border:2px solid #d9d9d9;color:var(--white);font-family:"Open Sans",sans-serif;font-size:14px;padding:10px 16px}
.submit{left:526px;top:2774px;width:154px;height:42px;font-size:17px;font-weight:700}

/* footer */
.footer{left:0;top:2900px;width:1200px;height:159px;background:var(--footer)}
.footer-brand{left:192px;top:2958px;display:flex;align-items:center;gap:8px;color:var(--white);font-size:24px;font-weight:500;white-space:nowrap}
.footer-square{width:10px;height:10px;background:var(--blue-bright)}
.footer-nav{left:382px;top:2945px;display:flex;gap:31px;font-size:15px;color:var(--white)}
.copy{left:382px;top:2980px;font-size:14.5px;color:#bdbdbd}
</style>
</head>
<body>
<div class="abs topbar"></div>
<header class="abs hero" role="img" aria-label="Blue glowing DNA double helix"></header>

<div class="abs brand">
  <span class="brand-square"></span>
  <span class="brand-name">Verantel</span>
</div>
<nav class="abs nav"><span>ABOUT US</span><span>OUR SERVICES</span><span>WHY US</span><span>BLOGS</span><span>NEWS</span><span>CONTACT US</span></nav>
<div class="abs social"><span></span><span></span><span></span></div>
<h1 class="abs hero-title">Medical Diagnostics<br>Consulting Services</h1>
<a class="abs btn hero-btn">LEARN MORE</a>
<div class="abs dots"><i></i><i></i><i></i></div>

<h2 class="abs section-title wwd-title">What We Do</h2>
<p class="abs wwd-lead">Pellentesque faucibus Ut accumsan ultricies elit Maecenas at justo id velit placerat<br>molestie Donec dictum lectus non odio Cras a ante vitae enim</p>

<div class="abs service" style="left:155px;top:1008px">
  <svg width="58" height="58" viewBox="0 0 58 58" style="top:50px" fill="none" stroke="#1a5cf2" stroke-width="2.2">
    <circle cx="26" cy="26" r="19"/><circle cx="26" cy="26" r="13"/><path d="M40 40l12 12"/>
    <circle cx="22" cy="23" r="3"/><circle cx="31" cy="22" r="2.5"/><circle cx="27" cy="31" r="3"/><path d="M24 25l2 4M29 23l-3 6"/>
  </svg>
  <h3 style="top:45px">Detection</h3>
  <p style="top:82px">Lorem ipsum dolor sit amet consectetuer adipiscing elit Nam cursus Morbi ut mi Nullam enim leo egestas id condimentum at laoreet</p>
  <a class="btn" style="top:196px">LEARN MORE</a>
</div>

<div class="abs service" style="left:475px;top:1004px">
  <svg width="58" height="58" viewBox="0 0 58 58" style="top:45px" fill="none" stroke="#1a5cf2" stroke-width="2.2">
    <rect x="14" y="10" width="22" height="40" rx="11" transform="rotate(35 25 30)"/>
    <circle cx="23" cy="26" r="2"/><circle cx="29" cy="33" r="2"/><circle cx="24" cy="36" r="1.5"/>
    <circle cx="9" cy="12" r="5"/><circle cx="50" cy="10" r="3"/><circle cx="8" cy="46" r="4"/><circle cx="48" cy="45" r="3"/>
  </svg>
  <h3 style="top:45px">Management of<br>Diseases</h3>
  <p style="top:102px">Lorem ipsum dolor sit amet consectetuer adipiscing elit Nam cursus Morbi ut mi Nullam enim leo egestas</p>
  <a class="btn" style="top:196px">LEARN MORE</a>
</div>

<div class="abs service" style="left:788px;top:1001px">
  <svg width="72" height="50" viewBox="0 0 72 50" style="top:50px;left:-34px" fill="none" stroke="#1a5cf2" stroke-width="2.2">
    <path d="M36 44L14 22a10 10 0 0 1 22-10a10 10 0 0 1 22 10z"/>
    <path d="M0 25h22l5-8 6 14 5-10 4 4h30"/>
  </svg>
  <h3 style="top:45px">Monitoring</h3>
  <p style="top:82px">Lorem ipsum dolor sit amet consectetuer adipiscing elit Nam cursus Morbi ut mi Nullam enim leo egestas id condimentum at laoreet</p>
  <a class="btn" style="top:196px">LEARN MORE</a>
</div>

<div class="abs about-photo" role="img" aria-label="Gloved hand adjusting a slide under a laboratory microscope"></div>
<section class="abs about-card">
  <h2>About Verantel Dx</h2>
  <p>tristique vitae consequat nec porta vel lectus Nulla sit amet diam Duis non nunc Nulla rhoncus dictum metus Curabitur</p>
  <p>tristique mi condimentum orci Phasellus pellentesque aliquam enim Proin dui lectus cursus eu mattis laoreet viverra sit amet quam Curabitur vel dolor ultrices ipsum dictum tristique</p>
  <a class="outline-btn">LEARN MORE</a>
</section>

<h2 class="abs section-title blog-title">Blogs &amp; News</h2>

<article class="abs post" style="left:160px">
  <div class="post-img" role="img" aria-label="Microscope in a bright laboratory" style="background:linear-gradient(135deg,#d9dee8,#f3f4f7 60%,#c8ccd6)"></div>
  <div class="post-date"><b>02</b><span>JAN</span></div>
  <h4>Pellentesque faucibus Ut accumsan ultric</h4>
  <p>Duis quam Nam eget lacus Aliquam erat volutpat Quisque dignissim congue leo Mauris vel lacus vitae felis vestibulum</p>
  <span class="more">READ MORE</span>
</article>
<article class="abs post" style="left:470px">
  <div class="post-img" role="img" aria-label="Ultrasound machine control panel" style="background:linear-gradient(135deg,#b9c3d6,#e4e8ef 55%,#7f8aa3)"></div>
  <div class="post-date"><b>02</b><span>JAN</span></div>
  <h4>Pellentesque faucibus Ut accumsan ultric</h4>
  <p>Duis quam Nam eget lacus Aliquam erat volutpat Quisque dignissim congue leo Mauris vel lacus vitae felis vestibulum</p>
  <span class="more">READ MORE</span>
</article>
<article class="abs post" style="left:786px">
  <div class="post-img" role="img" aria-label="Hospital monitoring equipment with a screen" style="background:linear-gradient(135deg,#4d6fc7,#9fb4e6 50%,#2b3f8f)"></div>
  <div class="post-date"><b>02</b><span>JAN</span></div>
  <h4>Pellentesque faucibus Ut accumsan ultric</h4>
  <p>Duis quam Nam eget lacus Aliquam erat volutpat Quisque dignissim congue leo Mauris vel lacus vitae felis vestibulum</p>
  <span class="more">READ MORE</span>
</article>

<section class="abs contact" role="img" aria-label="Dim scanner room in dark grey tones"></section>
<h2 class="abs section-title contact-title">Contact Us</h2>
<div class="abs field" style="left:260px;top:2566px;width:340px;height:42px">First Name</div>
<div class="abs field" style="left:608px;top:2566px;width:340px;height:42px">Last Name</div>
<div class="abs field" style="left:260px;top:2615px;width:340px;height:43px">Email address</div>
<div class="abs field" style="left:608px;top:2615px;width:340px;height:43px">Phone Number</div>
<div class="abs field" style="left:260px;top:2671px;width:688px;height:91px">Type Message</div>
<a class="abs btn submit">SUBMIT</a>

<footer class="abs footer"></footer>
<div class="abs footer-brand"><span class="footer-square"></span><span>Verantel</span></div>
<nav class="abs footer-nav"><span>ABOUT US</span><span>OUR SERVICES</span><span>WHY US</span><span>BLOGS</span><span>NEWS</span><span>CONTACT US</span></nav>
<p class="abs copy">© 2019 Company Name &nbsp;All right reserved</p>
</body>
</html>
```